New business card for a regional office of a US M&A company

We need business card for a finance company, office based in Hong Kong , our Head office is in US, our business is to Merge and acquires companies , the new office will be a regional office for the Asia Pacific region. We want to use the head office logo as attached ( but don't have to be exactly the same, can be a variation to it) as a base and then add Asia Pacific alongside the logo.
We would prefer to have be bilingual Eng + Chinese, although we don't really have Chinese company name .

Industry/Entity Type

Business

Contact Information for Business Card

Clara Jo Tsang
 

VP,
APAC M&A Operations
Orin Vantage Asia Pacific Limited
 
Unit 1407, K18
18 Tai Lok Shan Road, 
Hong Kong 
 
M: +852 6038 1742
T : +852 2836 4100
F : +852 2836 4177
VOIP: 4158
 
cjtsang@orinvantage.com

Font styles to use
Serif
Sans Serif

Colors

Designer to choose colors to be used in the design.

Requirements
Must have
• APAC Office

```html
<!DOCTYPE html>
<html lang="en">
<head>
<meta charset="utf-8">
<title>Orin Vantage Asia Pacific – Business Card</title>
<link rel="stylesheet" href="https://fonts.googleapis.com/css2?family=Ubuntu:wght@400;500;700&display=swap">
<style>
  :root {
    --navy: #0f2740;
    --navy-deep: #0c2036;
    --cyan: #27a9d1;
    --cyan-light: #2fb6dd;
    --cyan-dark: #1b98c3;
    --white: #ffffff;
    --silver: #c9ced3;
    --backdrop: #ebebeb;
  }
  * { margin: 0; padding: 0; box-sizing: border-box; }
  html, body { width: 1200px; height: 576px; overflow: hidden; }
  body {
    background: var(--backdrop);
    font-family: "Ubuntu", sans-serif;
    position: relative;
  }
  .card {
    position: absolute;
    top: 138px;
    width: 484px;
    height: 294px;
    border-radius: 12px;
    overflow: hidden;
  }

  /* Front */
  .card-front {
    left: 82px;
    background: var(--navy);
  }
  .card-front .accent-strip {
    position: absolute;
    left: 0; right: 0; bottom: 0;
    height: 7px;
    background: var(--cyan);
  }
  .card-front .brand-name {
    position: absolute;
    left: 0; right: 0;
    top: 124px;
    text-align: center;
    font-weight: 700;
    font-size: 34px;
    letter-spacing: 1px;
    color: var(--cyan);
  }

  /* Back */
  .card-back {
    left: 602px;
    background: linear-gradient(160deg, var(--cyan-light) 0%, var(--cyan) 55%, var(--cyan-dark) 100%);
  }
  .card-back .wave {
    position: absolute;
    left: 0; top: 0;
    width: 484px; height: 294px;
  }
  .holder { position: absolute; left: 18px; top: 32px; }
  .holder-name {
    font-weight: 500;
    font-size: 18px;
    color: var(--white);
    margin-bottom: 6px;
  }
  .holder-title {
    font-size: 12px;
    line-height: 15px;
    color: var(--navy);
  }
  .brand-block {
    position: absolute;
    right: 26px;
    top: 38px;
    text-align: right;
  }
  .brand-block .brand-name {
    font-weight: 700;
    font-size: 23px;
    letter-spacing: 0.5px;
    color: var(--navy);
  }
  .brand-block .brand-url {
    font-size: 9px;
    letter-spacing: 2.4px;
    color: var(--navy);
    margin-top: 1px;
  }
  .office {
    position: absolute;
    left: 18px;
    top: 140px;
  }
  .office-name {
    font-weight: 700;
    font-size: 13.5px;
    color: var(--white);
    margin-bottom: 6px;
  }
  .contact-list { list-style: none; }
  .contact-list li {
    display: flex;
    align-items: center;
    font-size: 12px;
    line-height: 15.5px;
    color: var(--navy);
  }
  .contact-list svg {
    width: 9px; height: 9px;
    margin-right: 10px;
    fill: var(--navy);
  }
</style>
</head>
<body>

<section class="card card-front" aria-label="Card front">
  <div class="brand-name">ORIN VANTAGE</div>
  <div class="accent-strip"></div>
</section>

<section class="card card-back" aria-label="Card back">
  <svg class="wave" viewBox="0 0 484 294" aria-hidden="true">
    <defs>
      <linearGradient id="silverBand" x1="0" y1="0" x2="1" y2="0">
        <stop offset="0" stop-color="#9ea6ad"/>
        <stop offset="0.45" stop-color="#e6e9ec"/>
        <stop offset="1" stop-color="#ffffff"/>
      </linearGradient>
    </defs>
    <path d="M0,228 C110,286 280,296 484,178 L484,294 L0,294 Z" fill="url(#silverBand)"/>
    <path d="M0,244 C120,298 290,298 484,192 L484,294 L0,294 Z" fill="#1fa3cf"/>
    <path d="M0,258 C130,300 300,288 484,204 L484,294 L0,294 Z" fill="var(--navy)"/>
    <path d="M60,262 C170,296 320,268 484,196" fill="none" stroke="#d7dbdf" stroke-width="2" opacity="0.7"/>
  </svg>

  <div class="holder">
    <div class="holder-name">Clara Jo Tsang</div>
    <div class="holder-title">Vice President,<br>APAC M&amp;A Operations</div>
  </div>

  <div class="brand-block">
    <div class="brand-name">ORIN VANTAGE</div>
    <div class="brand-url">www.orinvantage.com</div>
  </div>

  <div class="office">
    <div class="office-name">Orin Vantage Asia Pacific Limited</div>
    <ul class="contact-list">
      <li><svg viewBox="0 0 10 10"><rect x="2.5" y="0" width="5" height="10" rx="1"/></svg>+852 6038 1742</li>
      <li><svg viewBox="0 0 10 10"><path d="M0,3 Q5,-1 10,3 L8,4.5 L7,3 L3,3 L2,4.5 Z M2,5 L8,5 L9,10 L1,10 Z"/></svg>+852 2836 4100</li>
      <li><svg viewBox="0 0 10 10"><rect x="2" y="0" width="6" height="4"/><rect x="0" y="4" width="10" height="6" rx="1"/></svg>+852 2836 4177,&nbsp; VOIP: 4158</li>
      <li><svg viewBox="0 0 10 10"><path d="M0,2 L10,2 L10,8 L0,8 Z" /><path d="M0,2 L5,6 L10,2" fill="none" stroke="#27a9d1" stroke-width="0.8"/></svg>cjtsang@orinvantage.com</li>
    </ul>
  </div>
</section>

</body>
</html>
```